Company or website name
- dalewintham.com
- Links to the website
- Vita Forge
- Describe your company and organization and target audience
- Founded by celebrity personal trainer and media personality Dale Wintham, Vita Forge provides high quality on-site fitness and wellness classes, and personal trainers for businesses and residential gyms throughout New York City. Our target audience are residents of high end buildings in NYC, that expect excellence and luxury
- The design should have the following
- This is a 24"x36" Poster for a complimentary event at a high end building. I would like the poster to look high end, luxury and simple and chique. The words should be clear and easy to read. It would be great to have a final copy that we can send to the printer and one which we can edit for future events Here is the text: The Halcott Spires Gym Complimentary Fitness & Wellness Event Complimentary Yoga, Pilates & Interval Training Bootcamp Classes PLUS: 30 Minute Private Training Sessions *Kids Karate Classes Also Available Saturday May 18th, 25th & June 1st Time: 9:00am - 12:15pm Halcott Spires Gym Schedule: 9:00am - 9:30am Yoga 9:45am - 10:15am Interval Training Bootcamp 11:45am -12:15pm Pilates 9:00am - 12:00pm Private Training Sessions Special Introductory Rate on Future Packages During Promotion www.Vitaforge.tv Info@vitaforge.tv
- Other Facts

```html
<!DOCTYPE html>
<html lang="en">
<head>
<meta charset="utf-8">
<title>Halcott Spires Gym – Complimentary Fitness &amp; Wellness Event</title>
<link rel="stylesheet" href="https://fonts.googleapis.com/css2?family=Roboto+Condensed:ital,wght@0,700;1,700&family=Open+Sans:ital,wght@0,400;0,600;1,700&display=swap">
<style>
  :root {
    --canvas: #ffffff;
    --poster-black: #050505;
    --white: #ffffff;
    --orange: #f28a1e;
    --green: #8cc63f;
    --blue: #2aa0e0;
    --deep-blue: #1f3f9a;
    --skin-light: #c99a7a;
    --skin-dark: #6b4330;
  }
  * { margin: 0; padding: 0; box-sizing: border-box; }
  html, body { width: 1200px; height: 960px; overflow: hidden; background: var(--canvas); }
  .poster {
    position: absolute; left: 314px; top: 48px; width: 574px; height: 861px;
    background: var(--poster-black); overflow: hidden;
    font-family: "Open Sans", Arial, sans-serif; color: var(--white);
  }
  .swooshes { position: absolute; inset: 0; }
  .athlete-photo {
    position: absolute; left: 250px; top: 170px; width: 330px; height: 691px;
    background: radial-gradient(ellipse 45% 55% at 55% 45%, var(--skin-light) 0%, var(--skin-dark) 55%, rgba(5,5,5,0) 100%);
  }
  .brand {
    position: absolute; left: 440px; top: 20px; width: 125px; text-align: left;
  }
  .brand-mark { width: 52px; height: 52px; border-radius: 50%; background: var(--white); margin-bottom: 12px; }
  .brand-name { font-family: "Open Sans", Arial, sans-serif; font-weight: 600; font-size: 17px; color: var(--white); letter-spacing: 0.5px; line-height: 1.1; }
  .brand-by { font-weight: 400; font-size: 11px; color: var(--white); letter-spacing: 0.5px; margin-top: 3px; }
  .headline { position: absolute; left: 38px; top: 80px; font-family: "Roboto Condensed", "Arial Narrow", sans-serif; font-style: italic; font-weight: 700; }
  .headline-venue { font-size: 36px; line-height: 1; color: var(--white); }
  .headline-offer { font-size: 40px; line-height: 1.05; color: var(--green); padding-left: 88px; }
  .headline-event { font-size: 26px; line-height: 1.1; color: var(--blue); padding-left: 82px; }
  .lead {
    position: absolute; left: 24px; top: 216px; width: 330px;
    font-style: italic; font-weight: 700; font-size: 22px; line-height: 31px; color: var(--orange);
  }
  .rule { position: absolute; left: 22px; width: 330px; height: 2px; background: var(--white); }
  .rule-top { top: 312px; }
  .rule-bottom { top: 471px; }
  .plus {
    position: absolute; left: 24px; top: 326px;
    font-family: "Roboto Condensed", "Arial Narrow", sans-serif; font-weight: 700;
    font-size: 40px; line-height: 48px; color: var(--white);
  }
  .promo {
    position: absolute; left: 24px; top: 488px;
    font-style: italic; font-weight: 700; font-size: 21px; line-height: 31px; color: var(--green);
  }
  .schedule { position: absolute; left: 24px; top: 580px; }
  .schedule-title { font-weight: 600; font-size: 23px; line-height: 28px; color: var(--blue); }
  .schedule-list { list-style: none; font-size: 16px; line-height: 22.4px; }
  .schedule-list .label { color: var(--orange); font-weight: 600; }
  .schedule-list .time { color: var(--white); }
  .schedule-list .date { color: var(--green); font-weight: 600; }
  .contact {
    position: absolute; right: 12px; bottom: 6px;
    font-weight: 600; font-size: 15px; color: var(--white); word-spacing: 2px;
  }
</style>
</head>
<body>
<main class="poster">
  <div class="athlete-photo" role="img" aria-label="Photo of a smiling athlete in black sportswear throwing a punch toward the viewer"></div>

  <svg class="swooshes" viewBox="0 0 574 861" width="574" height="861" aria-hidden="true">
    <path d="M0 150 C90 70 220 20 330 0 L574 0 L574 0 L345 0 C230 30 110 85 0 175 Z" fill="var(--green)"/>
    <path d="M0 150 C100 70 220 25 330 0 L0 0 Z" fill="var(--deep-blue)"/>
    <path d="M0 120 C90 55 200 15 290 0 L0 0 Z" fill="var(--blue)" opacity="0.7"/>
    <path d="M574 680 C520 740 420 790 230 861 L574 861 Z" fill="var(--green)"/>
    <path d="M574 705 C520 765 440 810 300 861 L574 861 Z" fill="var(--deep-blue)"/>
    <path d="M574 740 C540 790 480 830 400 861 L574 861 Z" fill="var(--blue)" opacity="0.8"/>
  </svg>

  <div class="brand">
    <div class="brand-mark"></div>
    <div class="brand-name">VITA FORGE</div>
    <div class="brand-by">BY DALE WINTHAM</div>
  </div>

  <h1 class="headline">
    <span class="headline-venue">The Halcott Spires Gym</span><br>
    <span class="headline-offer">Complimentary</span><br>
    <span class="headline-event">Fitness &amp; Wellness Event</span>
  </h1>

  <p class="lead">Complimentary Yoga,<br>Pilates &amp; Interval Training<br>Bootcamp Classes</p>

  <div class="rule rule-top"></div>
  <p class="plus">PLUS: 30 Minute<br>Private Training<br>Sessions</p>
  <div class="rule rule-bottom"></div>

  <p class="promo">Special Introductory Rate<br>on Future Packages<br>During Promotion</p>

  <section class="schedule">
    <h2 class="schedule-title">Schedule:</h2>
    <ul class="schedule-list">
      <li class="label">Halcott Spires Gym</li>
      <li class="time">9:00am - 9:30am</li>
      <li class="label">Yoga</li>
      <li class="time">9:45am - 10:15am</li>
      <li class="label">Interval Training Bootcamp</li>
      <li class="time">11:45am -12:15pm</li>
      <li class="label">Pilates</li>
      <li class="time">9:00am - 12:00pm</li>
      <li class="label">Kids Karate Classes Also Available</li>
      <li class="date">Saturday May 18th, 25th &amp; June 1st</li>
      <li class="date">Time: 9:00am - 12:15pm</li>
    </ul>
  </section>

  <p class="contact">www.Vitaforge.tv Info@vitaforge.tv</p>
</main>
</body>
</html>
```